Luxury Wine Label for New Startup Winery

We need a wine label for our new winery startup. We have worked with a local designer but do not feel the resulting label / logo have the elevation required to present our brand as a luxury wine. Our winery is called "Quailbrook Vineyards" and we are focused on extremely high quality hand crafted artisan and estate wines from the Pacific Northwest.
We would like to see designs that utilize a tree line, or other imagery that represents the "Quailbrook" part of our company name. Another interesting feature could be wood grain.
A logo will be required based on your design so please design with this in mind:
This logo should be consistent with the wine bottle label design, and should be representative of our high end exclusive wine while giving a sense of place (Oregon/ Pacific Northwest.)
I will supply an image of the design we received from our local designer, PLEASE NOTE: in general we do like wood grain and tree line concepts but feel the execution was poorly done.
ATTN: Logo design should be suitable for use on: Bottles (Red wine/rose/white wine), Bussiness cards, vehicle signage, business signage, etc
P.S.:
If you have a design that is not outside the box we are still interested in seeing it.
Label is for a burgundy style bottle with a label height of 3.5 - 4" and a width of 3.5-4"
any label <= 4"x4" and >=3.5"x3.5" will be acceptable:
HOWEVER Width should be greater than or equal to height due to the bottle format
Target Market(s)
Wine enthusiasts with adequate discretionary budgets to afford $100 bottles of wine.
Industry/Entity Type
Wine / Winery
Requirements
Must have
- A sense of luxury, a feel of exclusivity, and a theme consistent with our product and brand name
Nice to have
- Tree line, wood grain or other wood themes. Serif fonts
Should not have
- anything cheesy, off topic, hard to read script fonts or anything that makes the label hard to read from a few feet away or too busy

```html
<!DOCTYPE html>
<html lang="en">
<head>
<meta charset="utf-8">
<title>Quailbrook Vineyards – Rosé Label</title>
<link rel="stylesheet" href="https://fonts.googleapis.com/css2?family=Cormorant+SC:wght@400;500&family=Jost:wght@400&display=swap">
<style>
  :root {
    --backdrop: #eef5f8;
    --label-paper: #f7f6f1;
    --label-paper-edge: #efede5;
    --ink: #111111;
    --rose-red: #e8101c;
    --grain-light: #e2c99c;
    --grain-tan: #c98a48;
    --grain-brown: #8a4a16;
    --grain-dark: #3a0d06;
    --grain-black: #0d0d0d;
  }
  * { margin: 0; padding: 0; box-sizing: border-box; }
  html, body {
    width: 766px;
    height: 1200px;
    overflow: hidden;
    background: var(--backdrop);
  }
  .label {
    position: absolute;
    left: 33px;
    top: 255px;
    width: 700px;
    height: 690px;
    background: linear-gradient(90deg, var(--label-paper) 0%, var(--label-paper) 60%, var(--label-paper-edge) 100%);
  }
  .wood-grain-art {
    position: absolute;
    left: 68px;
    top: 15px;
    width: 341px;
    height: 665px;
    background: linear-gradient(90deg,
      var(--grain-light) 0%,
      var(--grain-tan) 28%,
      var(--grain-brown) 50%,
      var(--grain-dark) 72%,
      var(--grain-black) 100%);
    opacity: 0.85;
  }
  .winery-name {
    position: absolute;
    left: 313px;
    top: 279px;
    width: 480px;
    height: 140px;
    transform: rotate(-90deg);
    transform-origin: center;
    font-family: "Cormorant SC", serif;
    font-weight: 500;
    font-size: 84px;
    line-height: 0.84;
    color: var(--ink);
    text-align: center;
    letter-spacing: 0.5px;
  }
  .winery-name span { display: block; }
  .wine-type {
    position: absolute;
    left: 452px;
    top: 592px;
    width: 200px;
    text-align: center;
    font-family: "Cormorant SC", serif;
    font-weight: 400;
    font-size: 46px;
    line-height: 1;
    color: var(--rose-red);
  }
  .vintage {
    position: absolute;
    left: 452px;
    top: 650px;
    width: 200px;
    text-align: center;
    font-family: "Jost", sans-serif;
    font-size: 19px;
    line-height: 1;
    color: var(--ink);
    letter-spacing: 0.5px;
  }
</style>
</head>
<body>
  <main class="label">
    <div class="wood-grain-art" role="img" aria-label="Stylised wood grain illustration in curving lines shading from pale tan through brown to black"></div>
    <h1 class="winery-name"><span>Quailbrook</span><span>Vineyards</span></h1>
    <p class="wine-type">Rose</p>
    <p class="vintage">2024</p>
  </main>
</body>
</html>
```